Brightcoat Painting Services Requires a New Responsive Site

Hi Designers,

Our current website is this www.brightcoatpainting.com.au for some idea.
I made it on Adobe Muse, its very basic.
I would like it to be redesigned to look more professional and also responsive. I actually know how to do html5 and css but I think others will do this much better than me.

I do not need content because I am a copywriter and would like to do all SEO and copy myself.

The most improtant things to remember is that the site cannot use a CMS
and the code needs to be understandable so that I can go in and add content later on and do SEO work.

Also the site requires an additional testimonial page. I would imagine a nice gallery would be a great addition too(something that I can add images too through html. Also in it is important for it to contain those brand images on the front page as it increases authority. I will attach them onto the brief.

Those two files of nearbyfind and tradeleafs are local directories where we have reviews so a placement of those on the testimonail page would make great sense. I will to the href myself.

Anyway, good luck!

I look forward to see your designs :D
Updates

I have just been informed that on this site websites are simply designed and not built (developed) if this is the case please stop working on your designs and spending more time on this project. I REQUIRE DEVELOPMENT ALSO AND HAVE ALREADY CONTACTED SUPPORT.

Target Market(s)

The target market is 30-75 high income earners.

Industry/Entity Type

Painting

Number of Pages Required

5+ page

Font styles to use
Serif
Sans Serif

Requirements
Must have
• attractive gallery, and the brand icons uploaded.
• must be responsive
• web carousel (with the different types of work we do). eg domestic, commercial, industrial etc.
Nice to have
• a little interactivity
• corporate a natural design that goes well with our logo
Should not have
• any content. just write jiberish to fill in the spaces.
• I will be doing all copy and SEO myself.
• More than five pages, bascially the four that already exist plus the testimonail one.

```html
<!DOCTYPE html>
<html lang="en">
<head>
<meta charset="utf-8">
<title>Brightcoat Painting Services</title>
<link href="https://fonts.googleapis.com/css2?family=Mulish:wght@400;600&family=Hind:wght@300;400&display=swap" rel="stylesheet">
<style>
:root{
  --header-top:#3b3b3b;
  --header-bottom:#1c1c1c;
  --footer:#222222;
  --ink:#222222;
  --muted:#555555;
  --sky:#4fb0e2;
  --button:#5bb5e8;
  --tile-border:#dddddd;
  --listing-blue:#00a7e6;
  --light:#f2f2f2;
}
*{box-sizing:border-box;margin:0;padding:0}
html,body{width:700px;height:1200px;overflow:hidden;background:#fff}
body{position:relative;font-family:"Mulish",sans-serif;color:var(--ink)}
.abs{position:absolute}

/* header */
.site-header{position:absolute;left:0;top:0;width:700px;height:100px;background:linear-gradient(var(--header-top),var(--header-bottom))}
.brand-mark{left:108px;top:8px;width:68px;height:56px;background:var(--sky);border-radius:3px}
.brand-name{left:70px;top:77px;width:144px;text-align:center;font-size:13px;color:var(--sky);font-weight:400}
.hotline{left:488px;top:19px;display:flex;align-items:center;gap:8px;color:#cfcfcf;font-size:14.5px}
.hotline-icon{width:22px;height:22px;border-radius:50%;background:#d8d8d8;display:flex;align-items:center;justify-content:center}
.main-nav{left:388px;top:64px;display:flex;gap:18px;font-size:10.5px;color:#fff}

/* hero */
.hero{left:0;top:100px;width:700px;height:341px;background:linear-gradient(90deg,#d3d4cf 0%,#c4c5bf 51%,#a5533a 51.5%,#8e432c 100%)}
.hero-arrow{width:32px;height:32px;border-radius:50%;background:rgba(70,70,70,.75);top:127px}
.hero-arrow.prev{left:22px}
.hero-arrow.next{left:642px;background:rgba(70,70,70,.35)}
.hero-caption{left:181px;top:126px;width:338px;height:37px;background:rgba(235,235,235,.7);font-size:23px;color:#333;text-align:center;line-height:37px}

/* welcome */
.welcome{left:0;top:455px;width:700px;text-align:center}
.welcome h1{font-size:20px;font-weight:400;line-height:24px}
.welcome .tagline{font-size:9px;line-height:12px}
.welcome p.intro{width:486px;margin:8px auto 0;font-size:8.6px;line-height:14px}
.read-more{display:inline-block;margin-top:8px;width:64px;height:22px;line-height:22px;background:var(--button);color:#fff;font-size:8px}

/* work carousel */
.work-card{background:#eee}
.work-photo{position:absolute;left:0;top:0;width:100%;height:100%}
.work-label{position:absolute;background:#fff;font-size:10.5px;padding-left:11px;line-height:25px;height:25px}
.work-feature{left:195px;top:578px;width:204px;height:170px;background:#f0f0f0;box-shadow:0 0 3px rgba(0,0,0,.2);z-index:2}
.work-feature .work-photo{height:118px;left:2px;top:2px;width:200px;background:linear-gradient(#7da6d6,#c7d4df 55%,#9aa0a4)}
.work-feature .work-title{position:absolute;left:8px;top:128px;font-size:10.5px}
.work-feature .work-note{position:absolute;left:8px;top:145px;width:192px;font-size:7px;line-height:9px}

/* brands */
.brands-title{left:0;top:745px;width:700px;text-align:center;font-size:20px;font-weight:400}
.brand-tile{top:793px;width:132px;height:61px;border:1px solid var(--tile-border);display:flex;align-items:center;justify-content:center;font-size:13px;font-weight:600;color:var(--ink)}
.brand-tile.listing{background:var(--listing-blue);border-color:var(--listing-blue);color:#fff}

/* footer */
.site-footer{left:0;top:862px;width:700px;height:338px;background:var(--footer);color:#fff;font-family:"Hind",sans-serif;font-weight:300}
.quote-heading{left:378px;top:28px;font-size:11px;font-weight:400}
.contact-heading{left:92px;top:62px;font-size:25px}
.contact-blurb{left:92px;top:104px;width:250px;font-size:10px;line-height:15.5px;font-weight:400}
.contact-item{display:flex;align-items:center;gap:8px;font-size:10.5px;font-weight:400}
.contact-icon{width:14px;height:14px;display:flex;align-items:center;justify-content:center}
.field{left:376px;width:267px;background:#fff;border-radius:2px;color:#aaa;font-size:10px;padding:9px 12px;font-weight:400}
.footer-rule{left:93px;top:292px;width:549px;height:1px;background:#3a3a3a}
.copyright{left:0;top:310px;width:700px;text-align:center;font-size:9px;font-weight:400;color:#ddd}
</style>
</head>
<body>

<header class="site-header">
  <div class="abs brand-mark"></div>
  <div class="abs brand-name">Brightcoat Painting</div>
  <div class="abs hotline">
    <span class="hotline-icon">
      <svg width="12" height="12" viewBox="0 0 24 24"><path d="M6.6 10.8a15 15 0 0 0 6.6 6.6l2.2-2.2a1 1 0 0 1 1-.25 11.4 11.4 0 0 0 3.6.57 1 1 0 0 1 1 1V20a1 1 0 0 1-1 1A17 17 0 0 1 3 4a1 1 0 0 1 1-1h3.5a1 1 0 0 1 1 1c0 1.25.2 2.45.57 3.57a1 1 0 0 1-.25 1z" fill="#444"/></svg>
    </span>
    1300 555 014
  </div>
  <nav class="abs main-nav"><span>Home</span><span>Services</span><span>Gallery</span><span>Contact Us</span></nav>
</header>

<section class="abs hero" role="img" aria-label="Living room with a grey sofa, framed pictures on a pale wall, a red brick feature wall and a floor lamp">
  <div class="abs hero-arrow prev">
    <svg width="32" height="32" viewBox="0 0 32 32"><path d="M19 8l-8 8 8 8" stroke="#bbb" stroke-width="1.5" fill="none"/></svg>
  </div>
  <div class="abs hero-arrow next">
    <svg width="32" height="32" viewBox="0 0 32 32"><path d="M13 8l8 8-8 8" stroke="#999" stroke-width="1.5" fill="none"/></svg>
  </div>
  <div class="abs hero-caption">Lorem ipsum dolor sit amet.</div>
</section>

<section class="abs welcome">
  <h1>Welcome</h1>
  <div class="tagline">Quality and Service</div>
  <p class="intro">Brightcoat Painting Services is a Melbourne family owned Painting &amp; Decorating business based in Berwick, in the south east of Melbourne. We proudly provide domestic and commercial painting services across all suburbs of metropolitan Melbourne.</p>
  <span class="read-more">Read more</span>
</section>

<div class="abs work-card" style="left:83px;top:618px;width:116px;height:113px">
  <div class="work-photo" role="img" aria-label="Row of white weatherboard townhouses" style="background:linear-gradient(#5a6f8a,#a3a9ae 60%,#6a6e70)"></div>
  <div class="work-label" style="left:0;top:79px;width:74px">Domestic</div>
</div>
<div class="abs work-card" style="left:399px;top:618px;width:79px;height:113px">
  <div class="work-photo" role="img" aria-label="Industrial building entrance with signage" style="background:linear-gradient(#c9d3dc,#b7b8b3 60%,#6f7a62)"></div>
  <div class="work-label" style="left:0;top:79px;width:40px;padding-left:0">rial</div>
</div>
<div class="abs work-card" style="left:481px;top:618px;width:130px;height:113px">
  <div class="work-photo" role="img" aria-label="Heritage red brick school building with a cross and trees" style="background:linear-gradient(90deg,#9a4632,#b25a3e 55%,#6f8a4a)"></div>
  <div class="work-label" style="left:0;top:79px;width:92px">Heritage</div>
</div>
<div class="abs work-feature">
  <div class="work-photo" role="img" aria-label="Large two storey white weatherboard home with a fountain"></div>
  <div class="work-title">Domestic</div>
  <div class="work-note">Brightcoat Painting we are focused on superior quality and workmanship</div>
</div>

<h2 class="abs brands-title">Our Brands</h2>
<div class="abs brand-tile" style="left:78px">Tallmark</div>
<div class="abs brand-tile" style="left:215px">Duraflo</div>
<div class="abs brand-tile" style="left:351px">Hollins</div>
<div class="abs brand-tile listing" style="left:487px">nearbyfind</div>

<footer class="abs site-footer">
  <div class="abs quote-heading">Contact Us Today Free Quotes</div>
  <div class="abs contact-heading">Contact Us</div>
  <p class="abs contact-blurb">Don't be shy, drop us an email and say hello! We are a really nice bunch of people :)</p>

  <div class="abs contact-item" style="left:96px;top:158px">
    <span class="contact-icon" aria-label="Phone"><svg width="10" height="16" viewBox="0 0 10 16"><rect x="1" y="1" width="8" height="14" rx="1.5" stroke="#fff" stroke-width="1.6" fill="none"/><circle cx="5" cy="12.5" r=".9" fill="#fff"/></svg></span>(416) 555-0000
  </div>
  <div class="abs contact-item" style="left:228px;top:158px">
    <span class="contact-icon" aria-label="Email"><svg width="15" height="11" viewBox="0 0 15 11"><rect width="15" height="11" fill="#fff"/><path d="M0 0l7.5 6L15 0" stroke="#222" stroke-width="1.3" fill="none"/></svg></span>hello@sitename.com
  </div>
  <div class="abs contact-item" style="left:96px;top:196px">
    <span class="contact-icon" aria-label="Short message profile"><svg width="15" height="14" viewBox="0 0 15 14"><path d="M2 1h11a1.5 1.5 0 0 1 1.5 1.5v6A1.5 1.5 0 0 1 13 10H6l-3.5 3V10H2A1.5 1.5 0 0 1 .5 8.5v-6A1.5 1.5 0 0 1 2 1z" fill="#fff"/></svg></span>@sitename
  </div>
  <div class="abs contact-item" style="left:228px;top:196px">
    <span class="contact-icon" aria-label="Social page"><svg width="14" height="14" viewBox="0 0 14 14"><circle cx="11" cy="2.5" r="2.2" fill="#fff"/><circle cx="3" cy="7" r="2.2" fill="#fff"/><circle cx="11" cy="11.5" r="2.2" fill="#fff"/><path d="M11 2.5L3 7l8 4.5" stroke="#fff" stroke-width="1.2" fill="none"/></svg></span>social.link/brightcoat
  </div>
  <div class="abs contact-item" style="left:96px;top:234px">
    <span class="contact-icon" aria-label="Community circle"><svg width="15" height="14" viewBox="0 0 15 14"><circle cx="5" cy="4" r="2.6" fill="#fff"/><path d="M0.5 13a4.5 4.5 0 0 1 9 0z" fill="#fff"/><circle cx="11" cy="5" r="2" fill="#fff"/><path d="M8.5 13a3.5 3.5 0 0 1 6 -2.5V13z" fill="#fff"/></svg></span>circle.link/sitename
  </div>
  <div class="abs contact-item" style="left:228px;top:234px">
    <span class="contact-icon" aria-label="Saved pins board"><svg width="11" height="15" viewBox="0 0 11 15"><path d="M5.5 0.5A5 5 0 0 1 10.5 5.5c0 3.5-5 9-5 9s-5-5.5-5-9a5 5 0 0 1 5-5z" fill="#fff"/><circle cx="5.5" cy="5.5" r="1.8" fill="#222"/></svg></span>pins.link/brightcoat
  </div>

  <div class="abs field" style="top:58px;height:30px">Your Name *</div>
  <div class="abs field" style="top:104px;height:30px">Your E-mail *</div>
  <div class="abs field" style="top:146px;height:123px">Your Message *</div>

  <div class="abs footer-rule"></div>
  <div class="abs copyright">© 2014 . www.companyname.com</div>
</footer>

</body>
</html>
```